Create an awesome website for a medical clinic

This is a new website for a doctor's office. The site should be clean and modern, easy to navigate.

This is a wellness clinic, we want to help our clients have a healthy, active lifestyle. It should be friendly and inviting, and easy for them to call or schedule an appointment.

The site should be responsive and designed using the attached Bootstrap 3 PSD.

We will provide stock photos, until then please use stock photos from:

pixelharbor.com or
framequarry.com (preferred)

Some example sites of clean and modern designs that we like:

https://tulsaspinecare.com/
http://reachpastjoints.com/
http://turninghealthier.com/

Also attached is a temporary logo you can use.

Reason: Thank you everyone for your great designs - we need a little more time so I'm extending the project.

Need extra days to review

Also, the colors in the new logo I just linked to are the final colors of the logo, so feel free to use any complimentary colors to it.

Hi everyone, The boss wants to change the layout of the site a little bit - here's the revised layout: https://www.filecrate.com/s/k9rt31vx2qp84zn/notes%2011_29_2017.pdf?dl=0 And the graphic assets you can use are here: https://www.filecrate.com/s/k9rt31vx2qp84zn/notes%2011_29_2017.pdf?dl=0 Feel free to change the background color of the "topbar", and change the icons of the "why people trust us" if you want, these are just temporary placeholders. Thanks for your patience and hard work!

Target Market(s)

People seeking medical treatment (wellness clinic)

Industry/Entity Type

Doctor

Number of Pages Required

1 page

Font styles to use
Sans Serif

Colors
0592cd
33a6d7
abd037
9bcb3c

Requirements
Must have
• The home page should have: a strong hero image/slideshow, clinic phone number should be prominent and at the top of the page (in the nav), a "what to expect" section (this is like a FAQs section - see attachment), and a strong call to action (a button to call or schedule an appointment).
• The what to expect section is useful so that prospective clients can determine if we're a good fit for them or not. It's a basic, first-step pre-qualification block of information.
• Social media icons which links to our social media profiles should be included.
Nice to have
• - Link to 3 most recent blog entries
• - Testimonials
• - How a multilevel nav menu looks.

```html
<!DOCTYPE html>
<html lang="en">
<head>
<meta charset="utf-8">
<title>Fernly — Wellness Clinic</title>
<link href="https://fonts.googleapis.com/css2?family=Roboto:ital,wght@0,300;0,400;0,500;0,700;0,900;1,400&display=swap" rel="stylesheet">
<style>
:root{
  --blue:#0592cd;
  --blue-soft:#33a6d7;
  --green:#9bcb3c;
  --green-bright:#abd037;
  --navy:#1f3f66;
  --ink:#2d5078;
  --muted:#8a9bb0;
  --line:#e6ebf1;
  --pale:#f5f7f9;
  --stage:#eceff3;
  --footer:#16304f;
}
*{box-sizing:border-box;margin:0;padding:0}
html,body{width:1200px;height:1200px;overflow:hidden;background:var(--stage);font-family:"Roboto",sans-serif;color:var(--ink)}
.stage{position:relative;width:1200px;height:1200px}
.page{position:absolute;left:443px;top:0;width:960px;height:3662px;background:#fff;transform:scale(.3277);transform-origin:0 0;overflow:hidden}
.wrap{width:887px;margin:0 auto;position:relative}
.section-title{font-weight:300;font-size:24px;color:var(--ink);position:relative;padding-bottom:12px}
.section-title::after{content:"";position:absolute;left:0;bottom:0;width:36px;height:3px;background:var(--green)}
.section-title.center{text-align:center}
.section-title.center::after{left:50%;margin-left:-18px}
.small{font-size:11px;line-height:1.55;color:#6c7f96}

/* top bar */
.topbar{height:34px;display:flex;align-items:center;justify-content:space-between;padding:0 60px;font-size:10px;color:var(--ink);border-bottom:1px solid var(--line)}
.social{display:flex;gap:10px}
.social span{width:12px;height:12px;border-radius:50%;border:1.5px solid #b9c4d1}

/* nav */
.nav{height:58px;display:flex;align-items:center;justify-content:space-between;padding:0 60px}
.brand{font-weight:900;font-size:20px;color:var(--green);letter-spacing:.5px}
.menu{display:flex;gap:34px;align-items:center;font-size:11px;color:var(--ink)}
.menu svg{width:14px;height:14px}

/* hero */
.hero{height:418px;position:relative;background:linear-gradient(90deg,#f4f5f7 0%,#eef0f3 100%)}
.hero-photo{position:absolute;right:0;top:0;width:640px;height:418px;background:linear-gradient(90deg,rgba(238,240,243,0) 0%,#e3ebf2 30%,#dbe6ef 60%,#e7eef4 100%)}
.hero-copy{position:absolute;left:58px;top:220px;width:380px}
.hero-kicker{font-size:11px;color:#a4b1c1;margin-bottom:8px}
.hero-title{font-weight:300;font-size:29px;line-height:1.15;color:var(--ink)}
.btn-light{display:inline-block;margin-top:22px;background:#fff;border-radius:22px;padding:12px 24px;font-size:10px;font-weight:700;color:var(--navy);letter-spacing:.4px;box-shadow:0 3px 10px rgba(30,60,100,.12)}

/* info band */
.info{height:178px;background:var(--blue);display:grid;grid-template-columns:235px 245px 1fr;gap:0 0;padding:30px 24px;color:#fff;font-size:10px}
.info h4{font-size:11px;font-weight:500;margin-bottom:18px;display:flex;align-items:center;gap:8px}
.info h4 svg{width:12px;height:12px}
.row{display:flex;justify-content:space-between;margin-bottom:13px;padding-right:40px}
.contact-line{display:flex;gap:10px;align-items:center;margin-bottom:13px}
.contact-line svg{width:10px;height:10px;flex:none}
.form{display:grid;grid-template-columns:repeat(3,1fr);gap:12px}
.field{height:30px;border:1.5px solid rgba(255,255,255,.75);border-radius:16px;padding:0 12px;display:flex;align-items:center;font-size:9px;color:rgba(255,255,255,.9)}
.field.wide{grid-column:span 2}
.send{height:30px;background:#fff;border-radius:16px;color:var(--blue);font-weight:700;font-size:9px;display:flex;align-items:center;justify-content:center}

/* about */
.about{height:594px;position:relative}
.about-copy{position:absolute;left:58px;top:62px;width:410px}
.about-copy .lead{margin:22px 0 26px}
.quote{font-weight:300;font-size:20px;color:#6a86a6;margin-bottom:30px}
.acc{border-bottom:1px solid var(--line);padding:14px 0}
.acc-head{display:flex;align-items:center;gap:12px;font-size:11px;font-weight:700;color:var(--ink)}
.acc-head svg.ico{width:18px;height:18px;flex:none}
.acc-head .arrow{margin-left:auto;width:12px;height:12px}
.acc-body{padding:12px 0 4px 30px}
.about-photo{position:absolute;right:58px;top:36px;width:340px;height:520px;background:linear-gradient(180deg,#f3f5f8 0%,#e6edf3 55%,#dde5ec 100%)}

/* facilities */
.facilities{height:322px;padding-top:46px}
.fac-grid{display:grid;grid-template-columns:repeat(6,1fr);gap:8px;width:887px;margin:36px auto 0}
.fac{text-align:center;padding:18px 10px 18px}
.fac.active{box-shadow:0 4px 18px rgba(30,60,100,.12)}
.fac svg{width:46px;height:46px;margin-bottom:12px}
.fac h5{font-size:12px;font-weight:500;color:var(--navy);margin-bottom:6px}
.fac p{font-size:10px;line-height:1.4;color:#7d8fa4}

/* stats */
.stats{height:145px;background:var(--blue);display:grid;grid-template-columns:repeat(4,1fr);align-items:center;color:#fff;text-align:center;padding:0 60px}
.stats b{display:block;font-size:24px;font-weight:400}
.stats span{font-size:10px;opacity:.85}

/* news */
.news{height:462px;padding-top:62px}
.news-grid{display:grid;grid-template-columns:repeat(4,1fr);gap:22px;width:846px;margin:34px auto 0}
.card{background:#fff;box-shadow:0 3px 14px rgba(30,60,100,.08)}
.thumb{height:150px}
.card-body{padding:14px 14px 12px}
.card h6{font-size:11px;font-weight:700;color:var(--ink);margin-bottom:6px}
.date{font-size:9px;color:#a1adbb;margin-bottom:8px}
.card .arrow{width:12px;height:12px;margin-top:8px;display:block}

/* testimonials */
.testi{height:358px;background:var(--pale);position:relative}
.testi-copy{position:absolute;left:60px;top:34px;width:480px}
.testi-head{font-weight:900;font-size:34px;line-height:1.15;color:var(--navy);margin:36px 0 14px;position:relative}
.marks{position:absolute;left:410px;top:-4px;font-size:60px;color:var(--green);line-height:1;font-weight:900;opacity:.5}
.testi-text{font-style:italic;font-size:11px;line-height:1.55;color:#7b8ea5;width:340px}
.author{font-size:10px;color:var(--ink);font-weight:500;margin-top:24px}
.author em{font-style:normal;color:#a1adbb;font-weight:400}
.dots{display:flex;gap:8px;align-items:center;margin-top:14px}
.dots i{width:8px;height:8px;border-radius:50%;background:#c9d3de}
.dots i.on{background:var(--blue)}
.dots svg{width:14px;height:12px;margin-left:60px}
.testi-photo{position:absolute;right:60px;top:40px;width:380px;height:318px;background:linear-gradient(180deg,#eef2f6 0%,#e2e8ef 100%)}

/* faq */
.faq{height:649px;padding-top:58px}
.faq-list{width:846px;margin:42px auto 0}
.faq-item{box-shadow:0 2px 10px rgba(30,60,100,.08);margin-bottom:22px;padding:22px 30px;display:flex;flex-wrap:wrap;align-items:center}
.faq-item .q{font-size:11px;font-weight:700;color:var(--ink);flex:1}
.faq-item svg{width:12px;height:12px}
.faq-item .a{flex-basis:100%;margin-top:10px}

/* map + footer */
.map{height:400px;background:linear-gradient(135deg,#e9edf1 0%,#f2f4f6 50%,#e4e9ee 100%);position:relative}
.map .pin{position:absolute;left:469px;top:180px;width:26px;height:34px}
.footer{height:44px;background:var(--footer);color:#fff;font-size:10px;display:flex;align-items:center;justify-content:center}
</style>
</head>
<body>
<div class="stage">
<main class="page">

  <div class="topbar">
    <span>For Emergency call 555.014.2290</span>
    <div class="social"><span></span><span></span><span></span><span></span></div>
  </div>

  <header class="nav">
    <div class="brand">FERNLY</div>
    <nav class="menu">
      <span>About Me</span><span>Medical Services</span><span>Departments</span><span>What to Expect</span><span>Contact</span>
      <svg viewBox="0 0 16 16" fill="none" stroke="#b3bfcc" stroke-width="1.6"><circle cx="7" cy="7" r="5"/><path d="M11 11l4 4"/></svg>
    </nav>
  </header>

  <section class="hero">
    <div class="hero-photo" role="img" aria-label="Smiling team of doctors and nurses in white coats"></div>
    <div class="hero-copy">
      <p class="hero-kicker">Suas munere corrumpit te quo</p>
      <h1 class="hero-title">Persius ponderum honestati squod postea vocent</h1>
      <span class="btn-light">WHAT TO EXPECT</span>
    </div>
  </section>

  <div class="wrap">
    <section class="info">
      <div>
        <h4><svg viewBox="0 0 12 12"><circle cx="6" cy="6" r="5.5" fill="#fff"/><path d="M6 3v3l2 1" stroke="#0592cd" stroke-width="1.2" fill="none"/></svg>Working Time</h4>
        <div class="row"><span>Monday - Friday</span><span>8:00 - 17:00</span></div>
        <div class="row"><span>Saturday</span><span>9:30 - 17:30</span></div>
        <div class="row"><span>Sunday</span><span>9:30 - 15:30</span></div>
      </div>
      <div>
        <h4><svg viewBox="0 0 12 12" fill="#fff"><path d="M2 1h3l1 3-2 1a7 7 0 0 0 3 3l1-2 3 1v3c-6 0-10-4-10-9z"/></svg>Contact Us</h4>
        <div class="contact-line"><svg viewBox="0 0 12 12" fill="#fff"><path d="M2 1h3l1 3-2 1a7 7 0 0 0 3 3l1-2 3 1v3c-6 0-10-4-10-9z"/></svg>555.014.2290</div>
        <div class="contact-line"><svg viewBox="0 0 12 12" fill="#fff"><rect x="1" y="2.5" width="10" height="7"/></svg>hello@fernlyclinic.com</div>
        <div class="contact-line"><svg viewBox="0 0 12 12" fill="#fff"><path d="M6 1 1 6h1.5v5h7V6H11z"/></svg>48 Harrow Lane, Easton, NY 10410</div>
      </div>
      <div>
        <h4><svg viewBox="0 0 12 12"><path d="M6 11s4-4 4-6.5a4 4 0 0 0-8 0C2 7 6 11 6 11z" fill="#fff"/></svg>Booking a visit</h4>
        <div class="form">
          <div class="field">Full Name</div><div class="field">Phone</div><div class="field">Date of Birth</div>
          <div class="field wide">Reason</div><div class="send">SEND</div>
        </div>
      </div>
    </section>
  </div>

  <section class="about">
    <div class="about-copy">
      <h2 class="section-title">About Me</h2>
      <p class="small lead">Id mollis instructior sit, his fuisset democritum ex, nibh docendi legendos ne sit. Eum diceret indoctum sed Persius ponderum, his fuisset democritum ex, nibh docendi legendos neum honestatis vel ad, quod postea vocent no vel.</p>
      <p class="quote">“Health is the most preciuos treasure”</p>
      <div class="acc">
        <div class="acc-head">
          <svg class="ico" viewBox="0 0 18 18" fill="#2d5078"><circle cx="9" cy="6" r="4"/><path d="M2 17c0-4 3-6 7-6s7 2 7 6z"/></svg>
          Experienced Physician
          <svg class="arrow" viewBox="0 0 12 12" fill="none" stroke="#9aa8b8" stroke-width="1.3"><path d="M6 11V1M2 5l4-4 4 4"/></svg>
        </div>
        <p class="small acc-body">Lorem ipsum dolor sit amet, cu decore efficiantur vis, possim melius vel ad. Ei vidisse minimum inciderint mel, an iusto corrumpit voluptatibus nec, eos pa rtem placerat disputationi in. Iusto dicant doctus sed in, sit putent diceret an, ludus ubique no nam. In veri decore dictas sit, nam eu nisl possit, pri erat placerat patrioque id.</p>
      </div>
      <div class="acc">
        <div class="acc-head">
          <svg class="ico" viewBox="0 0 18 18" fill="none" stroke="#2d5078" stroke-width="2"><path d="M3 15l9-9M10 4l4 4"/></svg>
          Complete Health Facilities
          <svg class="arrow" viewBox="0 0 12 12" fill="none" stroke="#9aa8b8" stroke-width="1.3"><path d="M1 6h10M7 2l4 4-4 4"/></svg>
        </div>
      </div>
      <div class="acc">
        <div class="acc-head">
          <svg class="ico" viewBox="0 0 18 18" fill="#2d5078"><rect x="1" y="3" width="16" height="10" rx="1"/><rect x="6" y="14" width="6" height="2"/></svg>
          Medical Standard Equipment
          <svg class="arrow" viewBox="0 0 12 12" fill="none" stroke="#9aa8b8" stroke-width="1.3"><path d="M1 6h10M7 2l4 4-4 4"/></svg>
        </div>
      </div>
    </div>
    <div class="about-photo" role="img" aria-label="Friendly doctor in a white coat with stethoscope holding a clipboard"></div>
  </section>

  <section class="facilities">
    <h2 class="section-title center">Facilities</h2>
    <div class="fac-grid">
      <div class="fac"><svg viewBox="0 0 46 46" fill="#2d5078"><rect x="6" y="10" width="14" height="24" rx="7" transform="rotate(-40 13 22)"/><circle cx="31" cy="14" r="7"/><circle cx="31" cy="32" r="8"/></svg><h5>Medicines</h5><p>Id mollis instructior sit, his fuisset</p></div>
      <div class="fac"><svg viewBox="0 0 46 46"><path d="M23 40 6 23a9 9 0 0 1 17-12 9 9 0 0 1 17 12z" fill="#2d5078"/><path d="M4 23h10l3-5 4 9 3-6h18" stroke="#fff" stroke-width="2" fill="none"/></svg><h5>Best Care</h5><p>Id mollis instructior sit, his fuisset</p></div>
      <div class="fac"><svg viewBox="0 0 46 46" fill="#2d5078"><rect x="4" y="12" width="38" height="28" rx="3"/><rect x="16" y="6" width="14" height="8" rx="2"/><circle cx="23" cy="26" r="8" fill="#fff"/><path d="M21 21h4v3h3v4h-3v3h-4v-3h-3v-4h3z"/></svg><h5>Research</h5><p>Id mollis instructior sit, his fuisset</p></div>
      <div class="fac active"><svg viewBox="0 0 46 46" fill="#2d5078"><rect x="3" y="14" width="4" height="24"/><rect x="3" y="28" width="40" height="5"/><rect x="39" y="24" width="4" height="14"/><rect x="9" y="22" width="9" height="6" rx="3"/><rect x="19" y="22" width="20" height="6"/><path d="M30 6h4v4h4v4h-4v4h-4v-4h-4v-4h4z"/></svg><h5>Bed Facility</h5><p>Id mollis instructior sit, his fuisset</p></div>
      <div class="fac"><svg viewBox="0 0 46 46" fill="#2d5078"><rect x="13" y="4" width="20" height="6"/><rect x="11" y="12" width="24" height="30" rx="2"/><path d="M21 19h4v5h5v4h-5v5h-4v-5h-5v-4h5z" fill="#fff"/></svg><h5>Safe Medication</h5><p>Id mollis instructior sit, his fuisset</p></div>
      <div class="fac"><svg viewBox="0 0 46 46" fill="#2d5078"><rect x="10" y="7" width="26" height="35" rx="2"/><rect x="17" y="4" width="12" height="6" rx="2"/><path d="M15 18h16M15 24h16M15 30h16M15 36h10" stroke="#fff" stroke-width="2"/></svg><h5>Reports</h5><p>Id mollis instructior sit, his fuisset</p></div>
    </div>
  </section>

  <section class="stats">
    <div><b>200%</b><span>Trustworthy</span></div>
    <div><b>2451</b><span>Patients in a year</span></div>
    <div><b>215</b><span>Awards Won</span></div>
    <div><b>24</b><span>Years of Experience</span></div>
  </section>

  <section class="news">
    <h2 class="section-title center">Latest News</h2>
    <div class="news-grid">
      <article class="card"><div class="thumb" role="img" aria-label="Park with trees and benches" style="background:linear-gradient(160deg,#b9c8a6,#6f7f5c)"></div><div class="card-body"><h6>First day in hospital</h6><p class="date">10 Dec, 2017</p><p class="small">Eum dicant indoctum et. Persius ponderum honestatis vel ad, quod postea vocent no vel.</p><svg class="arrow" viewBox="0 0 12 12" fill="none" stroke="#9aa8b8" stroke-width="1.3"><path d="M1 6h10M7 2l4 4-4 4"/></svg></div></article>
      <article class="card"><div class="thumb" role="img" aria-label="Young girl smiling outdoors" style="background:linear-gradient(160deg,#d9d0c2,#a99a84)"></div><div class="card-body"><h6>First day in hospital</h6><p class="date">10 Dec, 2017</p><p class="small">Eum dicant indoctum et. Persius ponderum honestatis vel ad, quod postea vocent no vel.</p><svg class="arrow" viewBox="0 0 12 12" fill="none" stroke="#9aa8b8" stroke-width="1.3"><path d="M1 6h10M7 2l4 4-4 4"/></svg></div></article>
      <article class="card"><div class="thumb" role="img" aria-label="Child playing in green garden" style="background:linear-gradient(160deg,#8fae6a,#3f5a2e)"></div><div class="card-body"><h6>First day in hospital</h6><p class="date">10 Dec, 2017</p><p class="small">Eum dicant indoctum et. Persius ponderum honestatis vel ad, quod postea vocent no vel.</p><svg class="arrow" viewBox="0 0 12 12" fill="none" stroke="#9aa8b8" stroke-width="1.3"><path d="M1 6h10M7 2l4 4-4 4"/></svg></div></article>
      <article class="card"><div class="thumb" role="img" aria-label="Swimmer in a turquoise pool" style="background:linear-gradient(160deg,#7cc7d2,#2b8fa3)"></div><div class="card-body"><h6>First day in hospital</h6><p class="date">10 Dec, 2017</p><p class="small">Eum dicant indoctum et. Persius ponderum honestatis vel ad, quod postea vocent no vel.</p><svg class="arrow" viewBox="0 0 12 12" fill="none" stroke="#9aa8b8" stroke-width="1.3"><path d="M1 6h10M7 2l4 4-4 4"/></svg></div></article>
    </div>
  </section>

  <section class="testi">
    <div class="testi-copy">
      <h2 class="section-title">Testimonials</h2>
      <h3 class="testi-head">KEEP YOUR HEAD UP<br>AND BE PATIENT<span class="marks">”</span></h3>
      <p class="testi-text">Justo dicant doctus sed in, sit putent diceret an, ludus ubique no nam. In veri decore dictas sit, nam eu nisl possit, pri erat placerat mollis instructior sit, his fuisset democritum ex, nibh docendi legendos ne sit.</p>
      <p class="author">Owen Hartley, <em>Happy Patient</em></p>
      <div class="dots"><i></i><i></i><i class="on"></i><i></i><svg viewBox="0 0 14 12" fill="none" stroke="#9aa8b8" stroke-width="1.3"><path d="M1 6h12M9 2l4 4-4 4"/></svg></div>
    </div>
    <div class="testi-photo" role="img" aria-label="Happy man in shirt and tie giving two thumbs up"></div>
  </section>

  <section class="faq">
    <h2 class="section-title center">FAQ</h2>
    <div class="faq-list">
      <div class="faq-item"><span class="q">Id mollis instructior sit, his fuisset democritum ex, nibh docendi legendos ne sit?</span><svg viewBox="0 0 12 12" fill="none" stroke="#9aa8b8" stroke-width="1.3"><path d="M6 11V1M2 5l4-4 4 4"/></svg><p class="small a">Justo dicant doctus sed in, sit putent diceret an, ludus ubique no nam. In veri decore dictas sit, nam eu nisl possit, pri erat placerat patrioque id. Id mollis instructior sit, his fuisset democritum ex, nibh docendi legendos ne sit. Eum diceret indoctum et. Persius ponderum honestatis vel ad, quod postea vocent no vel. Cu eos novum aliquid corrumpit.</p></div>
      <div class="faq-item"><span class="q">Eu cum eligendi voluptua perfecto. No brute laboramus reprehendunt pri, et sint ponderum quo?</span><svg viewBox="0 0 12 12" fill="none" stroke="#9aa8b8" stroke-width="1.3"><path d="M1 6h10M7 2l4 4-4 4"/></svg></div>
      <div class="faq-item"><span class="q">Quo omnis voluptaria ut, causae habemus ius at. Duo in etiam numquam lobortis, sed ne eligendi cotidieque?</span><svg viewBox="0 0 12 12" fill="none" stroke="#9aa8b8" stroke-width="1.3"><path d="M1 6h10M7 2l4 4-4 4"/></svg></div>
      <div class="faq-item"><span class="q">Suas munere corrumpit te quo, duo salutatus voluptatibus definitionem at?</span><svg viewBox="0 0 12 12" fill="none" stroke="#9aa8b8" stroke-width="1.3"><path d="M1 6h10M7 2l4 4-4 4"/></svg></div>
      <div class="faq-item"><span class="q">Justo dicant doctus sed in, sit putent diceret an, ludus ubique no nam. In veri decore dictas sit, nam eu nisl?</span><svg viewBox="0 0 12 12" fill="none" stroke="#9aa8b8" stroke-width="1.3"><path d="M1 6h10M7 2l4 4-4 4"/></svg></div>
    </div>
  </section>

  <section class="map" role="img" aria-label="Street map of the neighbourhood around the clinic">
    <svg class="pin" viewBox="0 0 26 34"><path d="M13 33S1 20 1 12a12 12 0 0 1 24 0c0 8-12 21-12 21z" fill="#0592cd"/><circle cx="13" cy="12" r="5" fill="#fff"/></svg>
  </section>

  <footer class="footer">© 2017 Copyright Fernly</footer>

</main>
</div>
</body>
</html>
```